Moravel Aesthetic Doctor

I require an elegant, luxurious looking business card for my aesthetic business. I am a doctor and that will set me aside from competitors. I am planning to provide home and spa based treatments to clients with high expectations. I have attached my logo.

```html
<!DOCTYPE html>
<html lang="en">
<head>
<meta charset="utf-8">
<title>Moravel Aesthetic Doctor – Business Card</title>
<link href="https://fonts.googleapis.com/css2?family=Cinzel:wght@400&family=Open+Sans:wght@300;400&display=swap" rel="stylesheet">
<style>
  :root {
    --stage: #e9e6e1;
    --card-white: #ffffff;
    --card-grey: #e6e6e6;
    --brand-blue: #1f7ac2;
    --brand-blue-deep: #1565a8;
    --accent-cyan: #29a9e0;
    --wave-light: #bfe3f5;
    --wave-mid: #5bb8e6;
    --text-grey: #7a7a7a;
    --text-white: #ffffff;
  }
  * { margin: 0; padding: 0; box-sizing: border-box; }
  html, body { width: 1200px; height: 1136px; overflow: hidden; }
  body {
    background: var(--stage);
    font-family: "Open Sans", sans-serif;
    position: relative;
  }
  .card {
    position: absolute;
    left: 250px;
    width: 700px;
    height: 400px;
    overflow: hidden;
    box-shadow: 0 10px 30px rgba(0,0,0,0.18);
  }
  .card--front {
    top: 118px;
    background: radial-gradient(ellipse at 70% 30%, var(--card-white) 40%, var(--card-grey) 100%);
  }
  .card--back {
    top: 618px;
    background: radial-gradient(ellipse at 50% 50%, var(--brand-blue) 55%, var(--brand-blue-deep) 100%);
  }
  .wave-art {
    position: absolute;
    left: 0;
    bottom: 0;
    width: 330px;
    height: 400px;
  }
  .details {
    position: absolute;
    left: 330px;
    top: 62px;
    color: var(--text-grey);
  }
  .details__name {
    font-size: 26px;
    font-weight: 400;
    color: var(--brand-blue);
    line-height: 1.1;
  }
  .details__letters {
    font-size: 11px;
    color: var(--accent-cyan);
    margin-left: 6px;
    letter-spacing: 0.3px;
  }
  .details__qualification {
    font-size: 14px;
    font-weight: 300;
    margin-top: 6px;
  }
  .details__rule {
    width: 34px;
    height: 2px;
    background: var(--accent-cyan);
    margin: 14px 0 12px;
  }
  .contact { list-style: none; font-size: 14px; font-weight: 300; }
  .contact li { display: flex; align-items: center; height: 24px; }
  .contact svg { width: 13px; height: 13px; margin-right: 12px; fill: var(--accent-cyan); }
  .social { display: flex; gap: 6px; height: 24px; align-items: center; }
  .social span { width: 13px; height: 13px; border-radius: 50%; background: var(--accent-cyan); }
  .services {
    margin-top: 20px;
    font-size: 14px;
    font-weight: 300;
    line-height: 24px;
  }
  .brand {
    position: absolute;
    left: 130px;
    top: 118px;
    display: flex;
    align-items: center;
    color: var(--text-white);
  }
  .brand__circle {
    width: 130px;
    height: 130px;
    border-radius: 50%;
    border: 3px solid var(--text-white);
    margin-right: 14px;
  }
  .brand__name {
    font-family: "Cinzel", serif;
    font-size: 62px;
    letter-spacing: 4px;
    line-height: 1;
  }
  .brand__sub {
    font-family: "Cinzel", serif;
    font-size: 24px;
    letter-spacing: 2px;
    margin-top: 6px;
  }
  .tagline {
    position: absolute;
    left: 0;
    right: 0;
    top: 300px;
    text-align: center;
    color: var(--text-white);
    font-size: 18px;
    font-weight: 300;
    letter-spacing: 0.5px;
  }
</style>
</head>
<body>
  <section class="card card--front">
    <svg class="wave-art" viewBox="0 0 330 400" role="img" aria-label="Flowing blue wave illustration of a woman's profile with streaming hair">
      <defs>
        <linearGradient id="waveFill" x1="0" y1="1" x2="1" y2="0">
          <stop offset="0" stop-color="#bfe3f5"/>
          <stop offset="0.5" stop-color="#5bb8e6"/>
          <stop offset="1" stop-color="#1f7ac2"/>
        </linearGradient>
      </defs>
      <path d="M0 150 C90 120 200 130 260 170 C300 200 320 260 330 320 L330 400 L0 400 Z" fill="url(#waveFill)"/>
    </svg>

    <div class="details">
      <h1 class="details__name">Dr Elise Varn<span class="details__letters">MRCPCH MD</span></h1>
      <p class="details__qualification">Australasian Diploma of Aesthetic Medicine</p>
      <div class="details__rule"></div>
      <ul class="contact">
        <li><svg viewBox="0 0 24 24"><path d="M6.6 10.8a15 15 0 0 0 6.6 6.6l2.2-2.2c.3-.3.7-.4 1-.2 1.1.4 2.3.6 3.6.6.6 0 1 .4 1 1V20c0 .6-.4 1-1 1A17 17 0 0 1 3 4c0-.6.4-1 1-1h3.5c.6 0 1 .4 1 1 0 1.3.2 2.5.6 3.6.1.3 0 .7-.2 1z"/></svg>0800 555 018</li>
        <li><svg viewBox="0 0 24 24"><path d="M2 5h20v14H2z M2 5l10 8 10-8" /></svg>elise@moravel.co.nz</li>
        <li><svg viewBox="0 0 24 24"><circle cx="12" cy="12" r="10"/></svg>www.moravel.co.nz</li>
        <li class="social"><span></span><span></span></li>
      </ul>
      <p class="services">Dermal injectables - Plasma facials<br>Microneedling - Skin boosters<br>Excessive sweating</p>
    </div>
  </section>

  <section class="card card--back">
    <div class="brand">
      <div class="brand__circle"></div>
      <div>
        <div class="brand__name">MORAVEL</div>
        <div class="brand__sub">AESTHETIC DOCTOR</div>
      </div>
    </div>
    <p class="tagline">Home and Spa Based Treatments</p>
  </section>
</body>
</html>
```